Label design - Superfood blend

We are a family owned nutrition company with big ambitions. Our goal is to develop a range of 100% natural supplements for women, inspired by nature & modern technology that helps them meet their nutritional needs while nourishing them from within. All our products are junk free because we believe that that’s how nature intended it. We also produce products through a sustainable process and only use biodegradable packaging for our products (See link - https://www.loamwrap.org.uk/biodegradable-stand-pouch-250g-kraft)

Our brand style is modern and minimalist. This same style will be reflected in our social media, website and we want it to be represented through the label designs for our product packaging.

We want some creative designers to design a label that is true to our style (See attached packaging brief with designs we like) and displays our values of Premium, High Quality, Organic Real Food supplements focused on women. I have provided examples in the attached brief, but please only use as inspiration, I dont want any of them to be copied (sorry have had my fingers burnt already !)
Updates

Hello all, Please note this design is for a LABEL and not the whole package. We will have a 500gm biodegradable brown package, and we will have a label (which is what this project is about) that will be stuck on the front. The size of the label will be a rectangle (unless you come up with a new shape) in the size 20cm * 15cm. Please do not submit designs for the WHOLE from of the package, as we dont intend to have printed packages. Regards

Hello all, I have added a new logo version to the attachments, could you please also try that version. Could you also please look at the new sliders. We are only looking for a minimlaist theme. If you dont know what that means, please do feel free to ask, I would be happy to supply examples. Minimalist designs, means clean, modern, upmarket, elegant designs. It does not use too many colors and mostly sticks to a combination of black and white with colors used sparingly. See some below for your reference anyway. https://www.pitchloft.co.uk/design/13359317 https://www.pitchloft.co.uk/design/17270649 https://www.pitchloft.co.uk/design/12584145 https://www.pitchloft.co.uk/design/12367479 https://www.snapquilt.com/search/pins/?q=minimalist%20label%20design&rs=rs&eq=&etslf=2809&term_meta[]=minimalist%7Crecentsearch%7Cundefined&term_meta[]=label%7Crecentsearch%7Cundefined&term_meta[]=design%7Crecentsearch%7Cundefined Regards

Target Market(s)

The target market is women between the age 25 to 45, based in UK (mostly based in larger cities in UK). They are typically middle class or higher and would be in demanding jobs and social lives, that requires for them to meet their nutrition needs in convenient, easy to take forms. The women would also be socially conscious and sensitive to issues like women's rights, environmental issues, healthy food, organic food and sustainability etc. I have a much more detailed customer avatar if required

Font styles to use
Serif
Sans Serif
Decorative
Script

Colors
e8e8e8
474747
1b1b1b
add136

Requirements
Must have
• The label, should look minimalist and modern, throw in some out of the box creativity and we have a winner. Creativity will definitely be of importance. Our packaging is a biodegradable brown paper stand up pouch (Example link in product description). So to make it standout from other colorful packaging - being creative would definitely help.
• Please use the color schemes provided in the brief (See attachments). But if you want to experiment I would be open to it, as long as they are still minimalist and does not stray very far from the color given in the brief :)

```html
<!DOCTYPE html>
<html lang="en">
<head>
<meta charset="utf-8">
<title>Verdalia – Glow Within label</title>
<link rel="stylesheet" href="https://fonts.googleapis.com/css2?family=Nunito:wght@400;600;700;800&display=swap">
<style>
  :root {
    --backdrop: #0c1a12;
    --pouch: #ececec;
    --label: #e6e8b4;
    --green: #5b8c2a;
    --green-soft: #6a9a35;
    --ink: #111111;
    --rule: #2a2a2a;
    --badge-dark: #1b1b1b;
    --badge-green: #3aa136;
  }
  * { margin: 0; padding: 0; box-sizing: border-box; }
  html, body {
    width: 923px; height: 1200px; overflow: hidden;
    background: var(--backdrop);
    font-family: "Nunito", "Helvetica Neue", Arial, sans-serif;
  }
  .pouch-front {
    position: absolute; left: 156px; top: 112px;
    width: 660px; height: 1088px;
    background: var(--pouch);
  }
  .label-main, .label-foot {
    position: absolute; left: 88px; width: 480px;
    background: var(--label);
  }
  .label-main { top: 0; height: 796px; }
  .label-foot { top: 820px; height: 268px; }

  .brand {
    position: absolute; left: 146px; top: 144px;
    width: 188px; height: 188px;
    border: 1.5px solid var(--green-soft); border-radius: 50%;
    display: flex; align-items: center; justify-content: center;
  }
  .brand-name {
    font-weight: 600; font-size: 17px; letter-spacing: 4px;
    color: #333; margin-top: 30px;
  }
  .title-main {
    position: absolute; left: 0; right: 0; top: 340px;
    text-align: center; font-weight: 700; font-size: 156px;
    line-height: 1; color: var(--green); letter-spacing: -2px;
  }
  .title-sub {
    position: absolute; left: 0; right: 0; top: 486px;
    text-align: center; font-weight: 800; font-size: 86px;
    line-height: 1; color: var(--ink); letter-spacing: -1px;
  }
  .subtitle {
    position: absolute; left: 0; right: 0; top: 584px;
    text-align: center; font-weight: 700; font-size: 22px;
    line-height: 29px; color: var(--green-soft);
  }
  .category {
    position: absolute; left: 120px; width: 240px; top: 664px;
    height: 56px; border-top: 1.5px solid var(--rule);
    border-bottom: 1.5px solid var(--rule);
    display: flex; align-items: center; justify-content: center;
    font-weight: 600; font-size: 23px; color: var(--green-soft);
  }
  .weight {
    position: absolute; left: 0; right: 0; top: 736px;
    text-align: center; font-weight: 700; font-size: 22px; color: var(--green-soft);
  }
  .cert-row {
    position: absolute; left: 0; right: 0; top: 40px;
    display: flex; justify-content: center; gap: 24px;
  }
</style>
</head>
<body>
  <main class="pouch-front">
    <section class="label-main">
      <div class="brand"><span class="brand-name">VERDALIA</span></div>
      <h1 class="title-main">GLOW</h1>
      <h2 class="title-sub">WITHIN</h2>
      <p class="subtitle">Organic, Plant-Based Prebiotics<br>and Superfood Blend</p>
      <p class="category">Food Supplement</p>
      <p class="weight">500gm</p>
    </section>
    <section class="label-foot">
      <div class="cert-row">
        <svg class="cert-badge" width="84" height="84" viewBox="0 0 84 84" role="img" aria-label="Organic certification badge">
          <circle cx="42" cy="42" r="39" fill="none" stroke="var(--badge-dark)" stroke-width="3"/>
        </svg>
        <svg class="cert-badge" width="84" height="84" viewBox="0 0 84 84" role="img" aria-label="Vegan certification badge">
          <rect x="6" y="6" width="72" height="72" fill="none" stroke="var(--badge-green)" stroke-width="3"/>
        </svg>
      </div>
    </section>
  </main>
</body>
</html>
```